KRBL informational brochure to aimed to attract people to all three our our service industries

This brochure is designed to be multi purposed, here are a few objectives:
1. To provide a receipt for septic services rendered onsite to customers. The receipt has coupons to entice each customer to use us in the future. This brochure also gives this customer tips on how to best keep their septic system from developing issues. By providing additional company information the septic customer can become educated about the other lines of service we provide in the area, i.e. Trash pick up, & roll-off dumpsters. Optimally we would want a septic customer to be so impressed with our septic work that they would trust us to serve them in the other areas we offer.
2. The brochure is a means of obtaining ratings and reviews for our online profiles, i.e. Zapmo, & Berta's roll. It is already hard enough to get a customer to give us 5-star ratings, so this is a useful tool to try and bait the customer to get a price reduction on their total cost for septic services by rating us or performing an online review. We want to have a place on the brochure that references our current 5-star ratings on Zapmo, Chatterpage, and Berta's roll see the attached example.
3. This brochure is not only useful for septic clients but can also be used for general advertising, we leave these brochures in a variety of public locations. Thus it would be efficient to show all lines of business and provide the information needed to acquire new clients.
4. Photographs are a critical component of our plan, customers like to SEE what we do and who we are. Thus, please find a creative way of including photos of what we offer by means of services and products. For individuals who have seen our brand around town, a photographic reminder might help this potential clients to recognizing who we are.
5. I will attach a copy of our last MakerBazaar project to this project to give you an idea of how we like to present ourselves.
6. We want to encourage the Spanish speaking individuals to call us for translated material.
7. We need to mention pricing on this brochure for all 3 lines of business, i'll find a way to provide those to you.
8. We don't know what size to choose, one size is 8.5'' x 11'' the other size is 8.5'' x 14'. Perhaps you can help us choose. not sure if we should have a trifold (3 pane) or quadfold (4 pane) brochure. We want to express ourselves creatively and not just provide boring information.
9. we need to have an american flag somewhere on display
Target Market(s)
Rural areas of North Texas, Our office is in Ponder TX and we serve 35 mile radius.
Industry/Entity Type
Waste Management

```html
<!DOCTYPE html>
<html lang="en">
<head>
<meta charset="utf-8">
<title>Kestrel Ridge Waste &amp; Septic Solutions – Trifold Brochure</title>
<link href="https://fonts.googleapis.com/css2?family=Libre+Baskerville&family=Open+Sans:wght@400;600;700&display=swap" rel="stylesheet">
<style>
:root{
  --yellow:#f6d000;
  --gold:#f3c300;
  --ink:#141414;
  --dark:#232323;
  --mid:#3b3b3b;
  --paper:#ffffff;
  --canvas:#d6d7d9;
  --red:#d4202a;
  --grey-line:#8a8a8a;
  --flag-navy:#3a4c86;
  --flag-red:#c0454d;
}
*{box-sizing:border-box;margin:0;padding:0}
html,body{width:879px;height:1200px;overflow:hidden}
body{background:var(--canvas);font-family:"Open Sans",sans-serif;position:relative}
.sheet{position:absolute;left:116px;width:648px;height:502px;box-shadow:0 10px 12px rgba(0,0,0,.28);overflow:hidden;background:var(--paper)}
.sheet--outside{top:67px}
.sheet--inside{top:622px;background:var(--dark)}
.panel{position:absolute;top:0;width:216px;height:502px;overflow:hidden}
.panel--1{left:0}.panel--2{left:216px}.panel--3{left:432px}
.abs{position:absolute}
.photo{position:absolute}

/* outside panel 1 */
.flag{left:105px;top:0;width:108px;height:88px;background:linear-gradient(135deg,var(--flag-navy),#d9d9de 55%,var(--flag-red))}
.overview{left:11px;top:98px;width:188px;border:1px solid #777;background:#fff;font-size:6.3px}
.overview__title{font-family:"Libre Baskerville",serif;font-size:10px;text-align:center;padding:3px 0;background:linear-gradient(#f4f4f4,#dcdcdc);border-bottom:1px solid #777}
.overview__row{display:flex;height:20px;border-bottom:1px solid #aaa}
.overview__label{width:72px;border-right:1px solid #aaa;padding:4px 2px}
.overview__notes{height:61px}
.coupon{left:11px;width:188px;border:1px dashed var(--yellow);text-align:center;font-size:9.5px;font-weight:600;line-height:1.55;color:var(--ink)}
.coupon em{font-style:normal;color:var(--gold)}
.coupon--rating{top:297px;height:64px;padding-top:9px}
.coupon--reminder{top:375px;height:59px;padding-top:12px}
.scissors{position:absolute;right:10px;top:-8px}
.spanish{left:0;width:216px;top:446px;text-align:center;color:var(--red);font-weight:700;font-size:10.5px}

/* bars */
.bar{position:absolute;left:0;bottom:0;width:648px;height:27px;background:var(--ink)}
.bar__quote{left:0;width:216px;top:8px;text-align:center;color:#fff;font-size:8.5px}
.bar__phone{left:216px;width:216px;top:6px;text-align:center;color:var(--yellow);font-weight:700;font-size:11px}
.bar__web{left:432px;width:216px;top:9px;text-align:center;color:#fff;font-size:5.6px}
.bar__web b{color:var(--yellow);font-weight:400}

/* outside panel 2 */
.panel--dark{background:linear-gradient(180deg,#0e0e0e,#2e2e2e 60%,#1f1f1f)}
.truck-circle{left:47px;top:10px;width:116px;height:116px;border-radius:50%;border:3px solid #fff;background:linear-gradient(180deg,#b9c9d9,#3a3a30 55%,#6a8a3e)}
.heading{position:absolute;left:0;width:216px;text-align:center;color:var(--gold);font-family:"Libre Baskerville",serif}
.copy{position:absolute;color:#fff;font-size:6.2px;line-height:1.42;text-align:justify}
.btn{left:50px;top:303px;width:112px;height:19px;border-radius:10px;background:var(--yellow);text-align:center;font-family:"Libre Baskerville",serif;font-size:11px;line-height:19px;color:var(--ink)}
.phone-big{left:0;width:216px;top:333px;text-align:center;color:var(--yellow);font-family:"Libre Baskerville",serif;font-size:17px}
.contact{left:0;width:216px;top:366px;text-align:center;color:#fff;font-size:8px;line-height:1.45}
.reviews{left:0;width:216px;top:443px;display:flex;justify-content:center;align-items:center;gap:5px;color:#fff;font-size:8px;font-weight:600}
.reviews .chip{width:12px;height:12px;background:var(--yellow)}

/* outside panel 3 */
.truck-photo{left:0;top:70px;width:216px;height:290px;background:linear-gradient(180deg,#7f93c9,#3a3a3a 45%,#b38b22 70%,#6f7b4a)}
.brand{left:14px;top:22px;display:flex;align-items:center;gap:9px}
.brand__mark{width:30px;height:30px;border-radius:50%;background:var(--yellow)}
.brand__name{font-family:"Libre Baskerville",serif;color:var(--gold);font-size:12.5px;line-height:1.45}
.badge{left:151px;top:117px;width:54px;height:54px;border-radius:50%;border:2px solid #fff;background:rgba(255,255,255,.35)}
.tagline{left:0;width:216px;top:386px;text-align:center;font-family:"Libre Baskerville",serif;font-size:12px;line-height:1.4;color:var(--ink)}
.blurb{left:30px;width:156px;top:432px;text-align:center;font-size:6.3px;line-height:1.5;color:#555}

/* inside */
.shot{position:absolute;top:0;height:250px}
.shot--trash{left:0;width:216px;background:linear-gradient(180deg,#a9c6e4,#e7c72a 55%,#6e7d55)}
.shot--dumpster{left:216px;width:216px;background:linear-gradient(180deg,#cfd9e2,#232323 45%,#77745f)}
.shot--septic{left:432px;width:216px;background:linear-gradient(180deg,#b8cde0,#3a3a30 45%,#c9a022 60%,#847b5d)}
.shot-circle{position:absolute;border-radius:50%;border:2px solid #fff}
.inside-overlay{position:absolute;left:0;top:0}
.service{position:absolute;top:0;width:216px;height:476px}
.service .heading{top:241px;font-size:13.2px;color:var(--gold)}
.rule{position:absolute;left:60px;width:96px;top:266px;height:1px;background:#8a8a8a}
.sub{position:absolute;left:0;width:216px;top:276px;text-align:center;color:var(--gold);font-size:6.7px}
.service .copy{left:14px;width:188px;font-size:6.8px}
.list{position:absolute;left:14px;width:190px;color:#fff;font-size:6.6px;line-height:1.68;list-style:none}
.list li::before{content:"• "}
.gold{color:var(--gold)}
.price-box{position:absolute;left:12px;top:295px;width:190px;height:37px;border:1px solid var(--gold);color:#fff;font-size:7.8px;font-weight:600;text-align:center;padding-top:5px;line-height:1.45}
.deals{position:absolute;left:0;bottom:0;width:648px;height:26px;background:var(--yellow);color:var(--ink);font-weight:700;font-size:12.3px;text-align:center;line-height:26px;white-space:nowrap}
</style>
</head>
<body>

<!-- OUTSIDE -->
<section class="sheet sheet--outside">
  <div class="panel panel--1" style="background:linear-gradient(90deg,#fff 70%,#efefef)">
    <svg class="abs" style="left:0;top:0" width="216" height="100" viewBox="0 0 216 100">
      <path d="M0,96 Q40,30 122,0 L140,0 Q55,35 0,86 Z" fill="#f6d000"/>
    </svg>
    <div class="abs flag" role="img" aria-label="Waving American flag"></div>

    <div class="abs overview">
      <div class="overview__title">Septic Service Overview</div>
      <div class="overview__row"><div class="overview__label">Today's Date</div></div>
      <div class="overview__row"><div class="overview__label">Next Service Date</div></div>
      <div class="overview__row"><div class="overview__label">System Type</div></div>
      <div class="overview__row"><div class="overview__label"># of gallons</div></div>
      <div class="overview__row"><div class="overview__label">Recommendations...</div></div>
      <div class="overview__notes"></div>
    </div>

    <div class="abs coupon coupon--rating">
      <svg class="scissors" width="34" height="14" viewBox="0 0 34 14"><g fill="none" stroke="#f6d000" stroke-width="2"><circle cx="27" cy="3.5" r="3"/><circle cx="27" cy="10.5" r="3"/><path d="M24,5 L2,11 M24,9 L2,3"/></g></svg>
      Give us a 5 star rating on Zapmo or<br>Berta's roll for <em>$10</em> off today's<br>cleaning services
    </div>
    <div class="abs coupon coupon--reminder">
      <svg class="scissors" width="34" height="14" viewBox="0 0 34 14"><g fill="none" stroke="#f6d000" stroke-width="2"><circle cx="27" cy="3.5" r="3"/><circle cx="27" cy="10.5" r="3"/><path d="M24,5 L2,11 M24,9 L2,3"/></g></svg>
      Save this Septic Reminder<br>for <em>$25 off</em> your next pumping!
    </div>
    <div class="abs spanish">Se Habla Español!!!</div>
  </div>

  <div class="panel panel--2 panel--dark">
    <svg class="abs" style="left:0;top:0" width="216" height="80" viewBox="0 0 216 80">
      <path d="M0,34 Q40,36 70,50" fill="none" stroke="#f6d000" stroke-width="3"/>
    </svg>
    <div class="abs truck-circle" role="img" aria-label="Septic pump truck parked on grass"></div>
    <div class="heading" style="top:157px;font-size:12.5px">Our Vision</div>
    <p class="copy" style="left:14px;width:188px;top:176px">To fully express our value of every customer's trust by means of operating under the utmost integrity, while also providing world class service; To grow in size and heart, yet never to outgrow a small-town experience.</p>
    <div class="heading" style="top:224px;font-size:12.5px">Our Team</div>
    <p class="copy" style="left:14px;width:188px;top:243px">Kestrel Ridge Waste Solutions is a family owned, faith based, business that started with just a truck and a dream. Kestrel Ridge Waste Solutions provides Residential curbside waste pickup, Roll-Off Dumpster Services and Septic System pumping.</p>
    <div class="abs btn">Contact Us</div>
    <div class="abs phone-big">
      <svg width="13" height="13" viewBox="0 0 24 24" style="vertical-align:-1px"><path fill="#f6d000" d="M6.6 10.8a15.1 15.1 0 0 0 6.6 6.6l2.2-2.2c.3-.3.7-.4 1-.2 1.1.4 2.3.6 3.6.6.6 0 1 .4 1 1V20c0 .6-.4 1-1 1A17 17 0 0 1 3 4c0-.6.4-1 1-1h3.5c.6 0 1 .4 1 1 0 1.3.2 2.5.6 3.6.1.3 0 .7-.2 1z"/></svg>
      (555)214-0377
    </div>
    <div class="abs contact">PO Box 112<br>Ashgrove, TX 75010<br>www.kestrelridgewaste.net<br>www.kestrelridgeseptic.net<br>kestrelridgewaste@mailbox.net</div>
    <div class="abs reviews">
      <span>Zapmo</span><span class="chip"></span><span>Berta's roll</span><span class="chip"></span><span>Chatterpage</span>
    </div>
  </div>

  <div class="panel panel--3">
    <div class="photo truck-photo" role="img" aria-label="Black and yellow septic truck flying American and Texas flags"></div>
    <svg class="abs" style="left:0;top:0" width="216" height="380" viewBox="0 0 216 380">
      <path d="M0,0 H216 V86 Q120,118 0,94 Z" fill="#141414"/>
      <path d="M0,94 Q120,118 216,86" fill="none" stroke="#f6d000" stroke-width="6"/>
      <path d="M0,340 Q110,366 216,328 V380 H0 Z" fill="#fff"/>
      <path d="M0,340 Q110,366 216,328" fill="none" stroke="#f6d000" stroke-width="5"/>
    </svg>
    <div class="abs brand">
      <span class="brand__mark"></span>
      <div class="brand__name">Kestrel Ridge Waste<br>&amp; Septic Solutions</div>
    </div>
    <div class="abs badge"></div>
    <div class="abs tagline">WE DON'T TALK TRASH,<br>WE TALK SOLUTIONS</div>
    <div class="abs blurb">Kestrel Ridge Waste Solutions is a family owned and operated business that started with one truck and a dream...</div>
  </div>

  <div class="bar">
    <svg class="abs" style="left:0;top:0" width="648" height="27" viewBox="0 0 648 27">
      <path d="M194,27 L206,0 H212 L200,27 Z M204,27 L216,0 H222 L210,27 Z" fill="#f6d000"/>
      <path d="M410,27 L422,0 H428 L416,27 Z M420,27 L432,0 H438 L426,27 Z" fill="#f6d000"/>
    </svg>
    <div class="abs bar__quote">CALL FOR YOUR FREE QUOTE</div>
    <div class="abs bar__phone">
      <svg width="11" height="11" viewBox="0 0 24 24" style="vertical-align:-1px;margin-right:4px"><circle cx="12" cy="12" r="10.5" fill="none" stroke="#f6d000" stroke-width="2"/><path fill="#f6d000" d="M9 7.5l1.6 2.4-1 1.2a7 7 0 0 0 3.3 3.3l1.2-1 2.4 1.6-.8 1.7c-4 0-8-4-8-8z"/></svg>555-214-0377
    </div>
    <div class="abs bar__web"><b>www.</b>kestrelridgewaste<b>.net</b> | <b>www.</b>kestrelridgeseptic<b>.net</b></div>
  </div>
</section>

<!-- INSIDE -->
<section class="sheet sheet--inside">
  <div class="shot shot--trash" role="img" aria-label="Yellow dumpster and black wheeled trash cart on gravel"></div>
  <div class="shot shot--dumpster" role="img" aria-label="Black roll-off dumpsters lined up on a lot"></div>
  <div class="shot shot--septic" role="img" aria-label="Septic truck pumping a tank on a rural property"></div>

  <svg class="inside-overlay" width="648" height="502" viewBox="0 0 648 502">
    <defs>
      <linearGradient id="darkFill" x1="0" y1="0" x2="0" y2="1">
        <stop offset="0" stop-color="#1a1a1a"/><stop offset="1" stop-color="#3a3a3a"/>
      </linearGradient>
    </defs>
    <path d="M0,194 Q108,168 216,182 Q330,196 432,224 Q540,240 648,204 V502 H0 Z" fill="url(#darkFill)"/>
    <path d="M0,194 Q108,168 216,182 Q330,196 432,224 Q540,240 648,204" fill="none" stroke="#f6d000" stroke-width="5"/>
    <rect x="215" y="0" width="2" height="476" fill="#000" opacity=".25"/>
    <rect x="431" y="0" width="2" height="476" fill="#000" opacity=".25"/>
  </svg>
  <div class="shot-circle" style="left:502px;top:164px;width:66px;height:66px;background:linear-gradient(#e6e0cf,#6f6650)" role="img" aria-label="Company door sticker on a service truck"></div>
  <div class="shot-circle" style="left:558px;top:142px;width:80px;height:80px;background:linear-gradient(#b9a07a,#6a5a3f)" role="img" aria-label="Tank locating equipment on the ground"></div>

  <div class="service" style="left:0">
    <div class="heading">Residential Waste Collections</div>
    <div class="rule"></div>
    <div class="sub">WE DON'T TALK TRASH, WE TALK SOLUTIONS!</div>
    <p class="copy" style="top:300px">Our local team provides professional, friendly, small-town customer service that you won't find anywhere else. There are multiple packages to meet any budget:</p>
    <ul class="list" style="top:348px">
      <li>Toters - starting at <span class="gold">$19.99</span>/ per month!</li>
      <li>2 yard Dumpsters – Start up special <span class="gold">$55</span> per month!</li>
      <li>Bagged Trash Service</li>
      <li>Bulk pick-up &amp; Garage clean outs</li>
      <li>See all the Discounts above!</li>
    </ul>
    <p class="copy" style="top:420px">We strive to offer dependable and affordable residential trash removal throughout Cedar County &amp; all the surrounding areas.</p>
    <div class="abs gold" style="left:14px;top:459px;font-size:6.8px">CALL FOR FREE QUOTE</div>
  </div>

  <div class="service" style="left:216px">
    <div class="heading">Roll-Off Dumpsters</div>
    <div class="rule"></div>
    <div class="sub">NO PROJECT IS TOO BIG!</div>
    <p class="copy" style="top:300px">KRBL offer a variety of roll-off and construction dumpsters that are ready to meet the needs of any construction or demolition project. From a small renovation or landscape project, to new building constructions.<br>We provide reliable waste hauling services:<br><span class="gold" style="font-weight:600">Staring at $450/ haul</span></p>
    <ul class="list" style="top:391px">
      <li>24-hour turn around time</li>
      <li>Competitive pricing</li>
      <li>Complementary Tonnage</li>
      <li>Friendly teammate always available to take your order</li>
    </ul>
  </div>

  <div class="service" style="left:432px">
    <div class="heading">Septic Pumping &amp; Cleaning</div>
    <div class="rule"></div>
    <div class="sub">SERVICE GARUNTEED OR YOUR WASTE BACK</div>
    <div class="price-box">Pump &amp; clean services starting at $350 for<br>conventional and $450 for aerobic systems!</div>
    <p class="copy" style="top:342px">We take pride in our work and are dedicated to offering the highest-quality septic pumping services available. From cesspools and septic tanks to sewage pits and beyond, you can depend on our experienced technicians to get the job done right. Sit back and relax while we take care of the dirty work.</p>
    <div class="abs gold" style="left:14px;top:413px;font-size:6.8px">Other Services</div>
    <ul class="list" style="top:424px">
      <li>Electronic tank location services</li>
      <li>Camera Snaking</li>
      <li>Emergency Septic Repairs</li>
      <li>Real Estate Septic Inspections</li>
    </ul>
  </div>

  <div class="deals">DISCOUNTS &amp; DEALS MILITARY, SENIOR, SEASONAL DISCOUNTS CLERGY HUGE REFERRAL BONUS</div>
</section>

</body>
</html>
```